TA BRAMLEY BUSINESS CARD DESIGN PROJECT

We need to utilize our logo that was expertly created on PixelHarbor and now need to match this with a business card design.

```html
<!DOCTYPE html>
<html lang="en">
<head>
<meta charset="utf-8">
<title>TA Bramley – Business Card</title>
<link rel="stylesheet" href="https://fonts.googleapis.com/css2?family=Montserrat:wght@400;500;700&display=swap">
<style>
  :root {
    --page-bg: #e6e2dd;
    --card-light: #efebe6;
    --card-dark: #1f1e1d;
    --brand-blue: #0f4c8f;
    --name-blue: #1d5797;
    --divider-white: #f4f1ec;
    --text-soft: #d3cec7;
    --icon-soft: #9aa7b6;
  }
  html, body {
    margin: 0;
    padding: 0;
    width: 1200px;
    height: 1047px;
    overflow: hidden;
    background: var(--page-bg);
  }
  .business-card {
    position: absolute;
    left: 100px;
    top: 252px;
    width: 1000px;
    height: 544px;
    display: block;
    filter: drop-shadow(0 10px 24px rgba(0,0,0,0.18));
  }
  .card-face { fill: var(--card-light); }
  .dark-panel { fill: var(--card-dark); stroke: var(--divider-white); stroke-width: 3; }
  .wave-band { fill: var(--brand-blue); }
  .brand-name {
    font-family: "Montserrat", sans-serif;
    font-weight: 700;
    font-size: 58px;
    letter-spacing: 4px;
    fill: var(--brand-blue);
  }
  .name-marker { fill: var(--brand-blue); }
  .person-name {
    font-family: "Montserrat", sans-serif;
    font-weight: 700;
    font-size: 26px;
    fill: var(--name-blue);
  }
  .contact-text {
    font-family: "Montserrat", sans-serif;
    font-weight: 400;
    font-size: 21px;
    fill: var(--text-soft);
  }
  .contact-icon { fill: var(--icon-soft); }
</style>
</head>
<body>
<svg class="business-card" viewBox="0 0 878 478" xmlns="http://www.w3.org/2000/svg" role="img" aria-label="TA Bramley business card for Owen Castell">
  <defs>
    <clipPath id="card-shape">
      <rect x="0" y="0" width="878" height="478" rx="18" ry="18"/>
    </clipPath>
  </defs>
  <g clip-path="url(#card-shape)">
    <rect class="card-face" x="0" y="0" width="878" height="478"/>

    <path class="dark-panel" d="M-4 92 C 150 72, 300 110, 430 225 C 530 315, 660 385, 882 385 L882 482 L-4 482 Z"/>

    <path class="wave-band" d="M0 44 C 150 30, 310 72, 445 195 C 535 278, 680 306, 878 298 L878 336 C 700 342, 560 320, 468 250 C 340 135, 200 78, 0 84 Z"/>
    <path class="wave-band" d="M545 322 C 660 362, 770 362, 878 352 L878 373 C 760 386, 640 376, 545 322 Z"/>
  </g>

  <text class="brand-name" x="845" y="168" text-anchor="end">TA BRAMLEY</text>

  <rect class="name-marker" x="0" y="205" width="25" height="55"/>
  <text class="person-name" x="38" y="226">OWEN CASTELL</text>
  <text class="contact-text" x="38" y="256">Managing Director</text>

  <text class="contact-text" x="38" y="306">Your address, City</text>
  <text class="contact-text" x="38" y="335">State, Zip 1234</text>

  <g class="contact-icon">
    <path d="M38 372 q9 -7 18 0 l-2 4 h-3 l-1 -3 h-6 l-1 3 h-3 z M40 378 h14 v7 h-14 z"/>
    <rect x="39" y="402" width="15" height="10" rx="1"/>
    <circle cx="46" cy="432" r="8"/>
  </g>
  <text class="contact-text" x="66" y="380">123 456 789</text>
  <text class="contact-text" x="66" y="409">info@youremail.com</text>
  <text class="contact-text" x="66" y="438">www.yourwebsite.com</text>
</svg>
</body>
</html>
```